Government Contracting business needs a website design.

Pellworth & Quine, LLC is a minority owned Service Disabled Veteran Owned Small Business (SDVOSB) that provides Strategic Planning, Public Health Emergency Response, and Data Management Solutions for Federal Civilian and Defense Agencies. We have over 20 years of experience helping health and defense agencies develop concept of operations, deploy assets and personnel in Hot Zones around the world, and deliver goods and services all of the globe.

We are a leader in the field of Data Management. We help our customers develop cloud migration and disaster recovery strategies. We are experts with database management, data replication, queries, consolidation, and records management.

We are looking for a very nice and simple website designs that states clearly what we do as a company and that is easy for our customers to follow. We would like to have some moving pictures that are base on our expertise. We want the website to be easy to use and have the scroll down features that keeps things all on the same page when clicking on the menu. I attached a document with what we need on the website. I will also attach our logo. We want it to look simple clean and very professional.

Target Market(s)

Government Contracting, Management Consulting, Health

Industry/Entity Type

Government

Coding

Coded - Design and coding required

Number of Pages Required

1 page

Font styles to use
Serif

Requirements
Must have
• Very nice picture slides that speaks to our capabilities in Disaster Response, Strategic Planning, and Database Management. Slick look and design. Make sure SDVOSB Logo is right at the beginning of website as our customers is looking for that certification. Very nice colors that blend well with our logo.
Nice to have
• Very nice and slick colors that blends well with logo.
Should not have
• Basic website design that are weary on the eye. No bright colors, just simple colors that looks good with logo.

```html
<!DOCTYPE html>
<html lang="en">
<head>
<meta charset="utf-8">
<title>Pellworth &amp; Quine, LLC</title>
<link href="https://fonts.googleapis.com/css2?family=Prata&family=Montserrat:wght@600;700&family=Open+Sans:wght@400;600&display=swap" rel="stylesheet">
<style>
:root{
  --navy:#1c2e3d;
  --navy-deep:#15232f;
  --teal:#2f4b5f;
  --teal-band:#3b5a6e;
  --grey-band:#eeeeee;
  --ink:#2b2b2b;
  --muted:#6b6b6b;
  --rule:#d6d6d6;
  --white:#ffffff;
  --accent:#c8a64a;
}
*{box-sizing:border-box;margin:0;padding:0}
html,body{width:1200px;height:4864px;overflow:hidden}
body{font-family:"Open Sans",Arial,sans-serif;color:var(--ink);background:var(--white);font-size:13px;line-height:1.6}
h1,h2,h3{font-family:"Prata",Georgia,serif;font-weight:400}
section,header,footer{position:relative;width:1200px}
.btn{display:inline-block;background:var(--teal);color:var(--white);font-family:"Montserrat",Arial,sans-serif;font-weight:600;font-size:13px;letter-spacing:1px;text-transform:uppercase;padding:12px 30px;border-radius:24px}
.photo{position:absolute}

/* Hero */
.hero{height:680px;overflow:hidden}
.hero .photo{inset:0;background:linear-gradient(120deg,#3c4d59 0%,#6f7c84 45%,#9aa3a8 70%,#55636c 100%)}
.hero .shade{position:absolute;inset:0;background:linear-gradient(90deg,rgba(20,32,42,.75) 0%,rgba(20,32,42,.35) 55%,rgba(20,32,42,.1) 100%)}
.topbar{position:absolute;top:0;left:0;right:0;height:80px;background:rgba(20,32,42,.55);display:flex;align-items:center;padding:0 60px}
.brand{display:flex;align-items:center;gap:12px;color:var(--white);font-family:"Prata",Georgia,serif;font-size:24px}
.brand .mark{width:26px;height:26px;background:var(--white)}
.nav{margin-left:auto;display:flex;gap:28px;font-family:"Montserrat",Arial,sans-serif;font-size:12px;font-weight:600;color:var(--white);letter-spacing:.5px}
.nav .active{border-bottom:2px solid var(--white);padding-bottom:4px}
.hero-copy{position:absolute;left:70px;top:320px;color:var(--white)}
.hero-copy h1{font-family:"Montserrat",Arial,sans-serif;font-weight:700;font-size:36px;line-height:1.25;max-width:680px;margin-bottom:26px}
.arrow{position:absolute;top:380px;width:40px;height:40px;border-radius:50%;background:rgba(255,255,255,.25)}
.arrow.l{left:16px}.arrow.r{right:16px}
.hero-curve{position:absolute;left:0;bottom:0}
.seal{position:absolute;left:835px;top:505px;width:150px;height:150px;border-radius:50%;background:var(--white);border:6px solid var(--teal);box-shadow:0 0 0 4px var(--white)}
.seal::after{content:"";position:absolute;inset:28px;border-radius:50%;background:#a33a3a}

/* Welcome */
.welcome{height:470px;text-align:center;padding-top:36px}
.welcome .mark{width:40px;height:40px;background:var(--teal);margin:0 auto 18px}
.welcome h2{font-size:34px;color:var(--ink);margin-bottom:20px}
.welcome p{width:900px;margin:0 auto 14px;color:var(--muted);font-size:13px}
.welcome .btn{margin-top:22px}

/* Capabilities */
.capabilities{height:640px;background:var(--grey-band);padding-top:70px}
.section-title{text-align:center;font-size:34px;margin-bottom:50px}
.cap-grid{display:grid;grid-template-columns:repeat(4,240px);gap:40px;margin-left:70px}
.cap .circle{width:200px;height:200px;border-radius:50%;margin:0 0 22px 10px;border:5px solid var(--white)}
.cap:nth-child(1) .circle{background:linear-gradient(135deg,#7fa8c9,#2b5a86)}
.cap:nth-child(2) .circle{background:linear-gradient(135deg,#3f5a6b,#1f3443)}
.cap:nth-child(3) .circle{background:linear-gradient(135deg,#3aa4d8,#0d3f78)}
.cap:nth-child(4) .circle{background:linear-gradient(135deg,#b9c6d0,#5d6d79)}
.cap h3{font-size:19px;line-height:1.25;margin-bottom:12px;min-height:48px}
.cap ul{list-style:none;font-size:12px;color:var(--muted)}
.cap li::before{content:"› ";color:var(--teal)}

/* Why hire */
.why{height:450px;overflow:hidden;margin-top:30px}
.why .photo{inset:0;background:linear-gradient(90deg,#15232f 0%,#1e3242 50%,#4b5d69 80%,#2a3b48 100%)}
.why .figure{position:absolute;left:700px;top:40px;width:340px;height:410px;background:linear-gradient(180deg,#56687a,#2d3e4c);border-radius:160px 160px 0 0}
.why-copy{position:absolute;left:120px;top:60px;color:var(--white);width:560px}
.why-copy h2{font-size:36px;margin-bottom:26px}
.why-copy ul{list-style:none;font-size:13px}
.why-copy li{margin-bottom:18px;padding-left:20px;position:relative}
.why-copy li::before{content:"";position:absolute;left:0;top:7px;width:7px;height:7px;border-radius:50%;background:var(--white)}
.why .badge{position:absolute;left:720px;top:40px;width:80px;height:80px;border-radius:50%;background:var(--accent);border:4px solid #8b7434}

/* Agencies */
.agencies{height:600px;padding-top:50px}
.agencies .section-title{margin-bottom:40px}
.agency-grid{display:grid;grid-template-columns:repeat(4,150px);column-gap:60px;row-gap:28px;justify-content:center}
.agency{height:90px;display:flex;align-items:center;justify-content:center}
.agency span{display:block;width:86px;height:86px;border-radius:50%}
.agency span.sq{border-radius:6px;width:110px;height:56px}
.agencies .more{display:block;text-align:center;margin-top:36px;font-family:"Prata",Georgia,serif;font-size:16px;line-height:1.5;text-decoration:underline;color:var(--ink)}

/* Join */
.join{height:590px;background:var(--teal-band);color:var(--white);text-align:center;padding-top:50px;overflow:hidden}
.join p{width:900px;margin:0 auto;font-size:13px;color:#d8e0e6}
.join .section-title{margin-bottom:26px}
.join .people{position:absolute;left:320px;bottom:0;width:560px;height:300px;background:linear-gradient(180deg,#6f8392,#2a3b48);border-radius:200px 200px 0 0}

/* Jobs */
.jobs{height:540px;padding:60px 0 0 70px;overflow:hidden}
.jobs h2{font-size:36px;margin-bottom:18px}
.jobs p{width:600px;color:var(--muted);font-size:13px;margin-bottom:24px}
.field{width:400px;height:40px;border:1px solid var(--rule);border-radius:3px;margin-bottom:14px;padding:10px 14px;font-size:12px;color:var(--muted);display:flex;justify-content:space-between}
.jobs .person{position:absolute;left:760px;top:30px;width:360px;height:510px;background:linear-gradient(180deg,#e8ecef,#c9d2d9);border-radius:180px 180px 0 0}

/* Contact */
.contact{height:380px;text-align:center;padding-top:30px;border-top:1px solid var(--rule)}
.contact h2{font-size:34px;margin-bottom:8px}
.contact .lead{color:var(--muted);font-size:13px;margin-bottom:30px}
.contact-form{display:flex;gap:22px;justify-content:center;text-align:left}
.contact-form .col{display:flex;flex-direction:column;gap:12px}
.input{width:310px;height:38px;border:1px solid var(--rule);padding:9px 12px;font-size:12px;color:var(--muted)}
.textarea{width:440px;height:138px;border:1px solid var(--rule);padding:9px 12px;font-size:12px;color:var(--muted)}
.contact .btn{margin-top:24px}

/* Footer */
.footer{height:480px;background:var(--navy);color:#c3ccd3}
.footer-curve{position:absolute;top:0;left:0}
.footer .seal{left:205px;top:-60px;width:140px;height:140px}
.footer-cols{position:absolute;top:140px;left:80px;display:grid;grid-template-columns:300px 250px 250px 260px;gap:20px}
.footer .brand{font-size:22px;margin-bottom:24px}
.social{display:flex;gap:12px}
.social span{width:34px;height:34px;border-radius:50%;border:1px solid #7e8d99}
.footer h3{font-size:18px;color:var(--white);margin-bottom:14px}
.footer ul{list-style:none;font-size:12px;line-height:2}
.footer li::before{content:"› "}
.copyright{position:absolute;bottom:0;left:0;right:0;height:64px;background:var(--navy-deep);display:flex;align-items:center;justify-content:center;font-size:12px;color:#9aa6b0}
</style>
</head>
<body>

<header class="hero" id="home">
  <div class="photo" role="img" aria-label="Business team meeting in an office"></div>
  <div class="shade"></div>
  <div class="topbar">
    <div class="brand"><span class="mark"></span>Pellworth &amp; Quine</div>
    <nav class="nav">
      <span class="active">HOME</span><span>ABOUT US</span><span>CAPABILITIES</span><span>WHY HIRE US?</span><span>AGENCIES WE SERVE</span><span>JOIN US</span><span>CONTACT</span>
    </nav>
  </div>
  <span class="arrow l"></span><span class="arrow r"></span>
  <div class="hero-copy">
    <h1>MISSION ORIENTED HEALTH IT AND ACQUISITION FOR THE DEFENSE AND VA COMMUNITY</h1>
    <span class="btn">Contact Us Today</span>
  </div>
  <svg class="hero-curve" width="1200" height="140" viewBox="0 0 1200 140"><path d="M0 140 L0 80 Q600 170 1200 40 L1200 140 Z" fill="#ffffff"/></svg>
  <div class="seal" role="img" aria-label="Veteran owned small business certification badge"></div>
</header>

<section class="welcome" id="about">
  <div class="mark"></div>
  <h2>Welcome To Pellworth &amp; Quine</h2>
  <p>Pellworth &amp; Quine, LLC is a minority owned Service Disabled Veteran Owned Small Business (SDVOSB) that provides Strategic Planning, Public Health Emergency Response, and Data Management Solutions for Federal Civilian and Defense Agencies. We have over 20 years of experience helping health and defense agencies develop concept of operations, deploy assets and personnel in Hot Zones around the world, and deliver goods and services all of the globe.</p>
  <p>We are a leader in the field of Data Management. We help our customers develop cloud migration and disaster recovery strategies. We are experts with database management, data replication, queries, consolidation, and records management.</p>
  <span class="btn">Learn More</span>
</section>

<section class="capabilities" id="capabilities">
  <h2 class="section-title">Core Capabilities</h2>
  <div class="cap-grid">
    <div class="cap">
      <div class="circle" role="img" aria-label="Planning team hands together"></div>
      <h3>Strategic Planning</h3>
      <ul><li>Organizational Needs Assessment</li><li>Roadmap Development</li><li>Marketing Outreach</li><li>Cost Benefit and Alternative Analysis</li><li>Leadership Training</li></ul>
    </div>
    <div class="cap">
      <div class="circle" role="img" aria-label="Emergency response analysis"></div>
      <h3>Public Health Emergency Response</h3>
      <ul><li>COOP Management</li><li>Disaster Relief Planning</li><li>Asset and Personnel Deployment</li><li>Financial Impact Analysis</li><li>Education Program Development</li><li>Community Outreach</li></ul>
    </div>
    <div class="cap">
      <div class="circle" role="img" aria-label="Data center server room"></div>
      <h3>Data Management Services</h3>
      <ul><li>Cloud Migration Strategy</li><li>Disaster Recovery Strategy</li><li>Records Management</li><li>Database Management and Consolidation</li><li>Data Analytics</li></ul>
    </div>
    <div class="cap">
      <div class="circle" role="img" aria-label="Delivery truck for contract logistics"></div>
      <h3>Contracts Vehicling</h3>
      <ul><li>SDVOSB Sole Source</li><li>GSA Schedule 70 (Sub)</li><li>GSA OASIS Pool 1 (Sub)</li><li>CIO SP3 (Sub)</li><li>CMS (Sub)</li></ul>
    </div>
  </div>
</section>

<section class="why" id="why">
  <div class="photo" role="img" aria-label="Dark technology background"></div>
  <div class="figure" role="img" aria-label="Professional using a virtual reality headset"></div>
  <div class="badge" role="img" aria-label="Years of experience badge"></div>
  <div class="why-copy">
    <h2>Why Hire Us?</h2>
    <ul>
      <li>Over 20 years of experience deploying assets and personnel to disaster zones around the US and the world</li>
      <li>Over 20 years of experience developing concept of operations and stakeholder management strategies for Federal Agencies</li>
      <li>Over 10 years of experience with database management and replications</li>
      <li>Highly educated consultants with over 90% possessing advance degrees and industry certifications</li>
    </ul>
  </div>
</section>

<section class="agencies" id="agencies">
  <h2 class="section-title">Agencies We Serve</h2>
  <div class="agency-grid" role="img" aria-label="Seals of federal agencies served">
    <div class="agency"><span style="background:#2d3e6b"></span></div>
    <div class="agency"><span class="sq" style="background:#2f5f9c"></span></div>
    <div class="agency"><span style="background:#3a5a9a"></span></div>
    <div class="agency"><span class="sq" style="background:#b13a3a"></span></div>
    <div class="agency"><span style="background:#4d5e3a"></span></div>
    <div class="agency"><span style="background:#3a5f8a"></span></div>
    <div class="agency"><span style="background:#8a9bb4"></span></div>
    <div class="agency"><span class="sq" style="background:#1f1f1f;width:66px;height:74px"></span></div>
    <div class="agency"><span class="sq" style="background:#3a3a3a"></span></div>
    <div class="agency"><span style="background:#7a7a7a"></span></div>
    <div class="agency"><span style="background:#2f6a4a"></span></div>
    <div class="agency"><span style="background:#a83232"></span></div>
  </div>
  <a class="more">Learn More about Research Publications</a>
</section>

<section class="join" id="join">
  <h2 class="section-title">Join Us</h2>
  <p>Pellworth &amp; Quine strives to provide an outstanding work environment for our employees. We invest in our people and believe strongly in creating an environment where our employees are free to work on innovative solutions that meet our clients' needs. We provide true work-life balance, career advancement, health, and financial security and fun in the work place. We encourage our employees to participate in our internal operation and help to develop them into the ideal consultants that our clients seek.</p>
  <div class="people" role="img" aria-label="Group of smiling business professionals"></div>
</section>

<section class="jobs">
  <h2>Job Openings.</h2>
  <p>We are always recruiting for key positions. If you want to bring your talents to us, submit your resume against the key positions we have below. We are recruiting junior, mid level, senior as well as subject matter experts. Just send your qualified resume our way and we will find a way to bring you on board.</p>
  <div class="field"><span>Select Capability</span><span>▾</span></div>
  <div class="field"><span>Upload Your Resume</span><span>✎</span></div>
  <span class="btn">Apply Now</span>
  <div class="person" role="img" aria-label="Smiling professional holding a tablet"></div>
</section>

<section class="contact" id="contact">
  <h2>Contact Us</h2>
  <p class="lead">For information about teaming with us and our capabilities, please drop us a message.</p>
  <div class="contact-form">
    <div class="col"><div class="input">Name *</div><div class="input">Email *</div><div class="input">Phone *</div></div>
    <div class="textarea">Message *</div>
  </div>
  <span class="btn">Submit</span>
</section>

<footer class="footer">
  <svg class="footer-curve" width="1200" height="70" viewBox="0 0 1200 70"><path d="M0 0 L1200 0 L1200 10 Q600 90 0 30 Z" fill="#ffffff"/></svg>
  <div class="seal" role="img" aria-label="Veteran owned small business certification badge"></div>
  <div class="footer-cols">
    <div>
      <div class="brand"><span class="mark"></span>Pellworth &amp; Quine</div>
      <div class="social"><span></span><span></span><span></span></div>
    </div>
    <div>
      <h3>Sitemap</h3>
      <ul><li>Home</li><li>About Us</li><li>Capabilities</li><li>Why Hire Us</li><li>Agencies We Serve</li><li>Join Us</li><li>Contact Us</li></ul>
    </div>
    <div>
      <h3>Capabilities</h3>
      <ul><li>Strategic Planning</li><li>Public Health Emergency Response</li><li>Data Management Services</li><li>Contracts Vehicles</li></ul>
    </div>
    <div>
      <h3>Contact Us</h3>
      <ul><li>Pellworth &amp; Quine</li><li>4100 Larkmoor Drive, Suite 12</li><li>Arlen, VA 22000</li><li>(555) 014-2290</li><li>info@pellworthquine.com</li></ul>
    </div>
  </div>
  <div class="copyright">©Pellworth &amp; Quine - 2016 All Right Reserved.</div>
</footer>

</body>
</html>
```